Honey Company from Florida Needs Sweet and Buzz-worthy Site

Website Requests:
-Deluxe 5-Page Website with SSL-Secure Online Store (Shopify)
-High-end imagery to appeal to a discerning consumer
-Detailed verbiage with strong SEO and easy readability
-Design principles: simple, chic, luxe, earthy
Pages:
1. Home {Local, Raw American Honey from Florida}
2. The Hive
> About Us
>Meet the Beekeepers
3. Buy Honey
> Shopify retail store
4. The Buzz {News, Recipes & More}
> Blog
5. Contact Us {We're Buzzin' to Meet You}
> Store Hours
> Phone Number
> Address
> Quick Contact Form
Attachments: Web design notes, Logo, Color Codes, Inspiration Photos
Target Market(s)
High-end honey consumer in the U.S.
Industry/Entity Type
Upscale honey enthusiasts; direct to consumer sales.
Coding
Coded - Design and coding required
Number of Pages Required
5+ page
Requirements
Must have
- Upscale look and feel, easy usability for quick sales.

```html
<!DOCTYPE html>
<html lang="en">
<head>
<meta charset="utf-8">
<title>Amber Grove Honey Co.</title>
<link href="https://fonts.googleapis.com/css2?family=Roboto:wght@400;500;700&display=swap" rel="stylesheet">
<style>
:root{
  --honey:#ecc452;
  --ink:#111111;
  --text:#3c3c3c;
  --muted:#5a5a5a;
  --white:#ffffff;
  --footer-bar:#1c1c1c;
  --line:#dddddd;
  --amber:#e39a22;
  --amber-deep:#b8621a;
  --wood:#6b3d1e;
  --wood-dark:#3a200f;
}
*{margin:0;padding:0;box-sizing:border-box}
html,body{width:1200px;height:4521px;overflow:hidden;background:var(--white);font-family:'Roboto',Arial,sans-serif;color:var(--text)}
.page{position:relative;width:1200px;height:4521px}
section,header,footer{position:absolute;left:0;width:1200px}
.abs{position:absolute}

/* hero */
.hero{top:0;height:684px;overflow:hidden;
  background:
    radial-gradient(ellipse 260px 300px at 720px 380px,rgba(226,128,22,.95),rgba(226,128,22,0) 100%),
    radial-gradient(ellipse 230px 170px at 150px 470px,rgba(232,170,60,.85),rgba(232,170,60,0) 100%),
    radial-gradient(ellipse 160px 160px at 1110px 470px,rgba(170,110,50,.8),rgba(170,110,50,0) 100%),
    radial-gradient(ellipse 700px 260px at 600px 110px,rgba(196,150,90,.9),rgba(196,150,90,0) 100%),
    linear-gradient(180deg,#8a5a2e 0%,#6d3d1a 45%,#7a4421 70%,#4a2712 100%)}
.hero-shade{left:0;top:0;width:1200px;height:684px;background:linear-gradient(180deg,rgba(0,0,0,.15) 0%,rgba(0,0,0,0) 30%,rgba(0,0,0,0) 70%,rgba(30,12,4,.45) 100%)}
.logo{left:110px;top:26px;width:176px;height:176px;border-radius:50%;background:var(--white);display:flex;align-items:center;justify-content:center;text-align:center;font-weight:700;color:var(--ink);font-size:22px;line-height:1.2;padding:20px}
.nav{left:463px;top:40px;width:625px;height:42px;border-bottom:1px solid rgba(255,255,255,.75)}
.nav a{color:var(--white);text-decoration:none;font-size:13px;font-weight:700;position:absolute;top:10px}
.nav svg{position:absolute;top:9px}
.hero-title{top:281px;left:0;width:1200px;text-align:center;color:var(--white);font-size:43px;font-weight:700;line-height:52px;text-transform:uppercase;text-shadow:0 2px 10px rgba(0,0,0,.25)}
.btn{display:inline-flex;align-items:center;justify-content:center;background:var(--honey);color:#222;font-weight:700;font-size:13px;border-radius:24px;text-transform:uppercase}
.hero .btn{position:absolute;left:528px;top:447px;width:144px;height:44px}
.dots{left:574px;top:617px;display:flex;gap:7px}
.dots span{width:12px;height:12px;border-radius:50%;border:2px solid var(--white)}

/* importance */
.importance{top:684px;height:609px}
.importance .photo{left:598px;top:0;width:602px;height:609px;
  background:
    radial-gradient(ellipse 190px 200px at 260px 380px,rgba(190,70,10,.95),rgba(190,70,10,0) 100%),
    radial-gradient(ellipse 120px 180px at 540px 420px,rgba(240,190,70,.9),rgba(240,190,70,0) 100%),
    radial-gradient(ellipse 80px 140px at 230px 110px,rgba(245,175,50,.9),rgba(245,175,50,0) 100%),
    linear-gradient(170deg,#c9a264 0%,#a77a3c 45%,#5a3418 100%)}
.importance h2{left:110px;top:80px;font-size:35px;font-weight:700;color:var(--ink)}
.importance .kicker{left:110px;top:131px;font-size:16px;color:#333}
.importance .lead{left:110px;top:165px;width:420px;font-size:16px;line-height:22px;color:#222}
.importance .body{left:110px;top:222px;width:440px;font-size:13px;line-height:21.5px;color:var(--muted)}
.importance .body p{margin-bottom:21px}
.importance .btn{position:absolute;left:110px;top:497px;width:146px;height:46px}

/* description */
.description{top:1293px;height:829px}
.description h2{top:96px;width:1200px;text-align:center;font-size:34px;font-weight:700;color:var(--ink)}
.desc-item{font-size:12.5px;line-height:21px;color:var(--muted);width:270px}
.desc-item.left{text-align:right}
.desc-icon{width:64px;height:64px}
.desc-photo{left:455px;top:245px;width:315px;height:270px;
  background:
    radial-gradient(ellipse 150px 90px at 150px 140px,rgba(240,150,30,1),rgba(240,150,30,0) 100%),
    radial-gradient(ellipse 60px 40px at 140px 210px,rgba(90,150,40,.8),rgba(90,150,40,0) 100%),
    radial-gradient(ellipse 158px 125px at 50% 52%,#f0ad3a 0%,#e0901f 60%,rgba(255,255,255,0) 100%)}

/* video */
.video{top:2122px;height:472px;
  background:
    radial-gradient(ellipse 220px 220px at 620px 220px,rgba(240,175,60,.95),rgba(240,175,60,0) 100%),
    radial-gradient(ellipse 260px 280px at 960px 280px,rgba(236,160,30,1),rgba(236,160,30,0) 100%),
    radial-gradient(ellipse 120px 80px at 930px 40px,rgba(210,130,30,.9),rgba(210,130,30,0) 100%),
    linear-gradient(95deg,#8a5632 0%,#a66d3e 35%,#c98f4d 60%,#b5762f 100%)}
.play{left:552px;top:188px;width:96px;height:96px;border-radius:50%;background:rgba(255,255,255,.45);display:flex;align-items:center;justify-content:center}
.play span{width:66px;height:66px;border-radius:50%;background:var(--white);display:flex;align-items:center;justify-content:center}

/* health */
.health{top:2594px;height:453px}
.health .photo{left:0;top:0;width:602px;height:453px;
  background:
    radial-gradient(ellipse 120px 90px at 110px 270px,rgba(230,160,50,.95),rgba(230,160,50,0) 100%),
    radial-gradient(ellipse 90px 80px at 330px 170px,rgba(200,130,30,.95),rgba(200,130,30,0) 100%),
    radial-gradient(ellipse 80px 90px at 450px 250px,rgba(240,200,80,.9),rgba(240,200,80,0) 100%),
    radial-gradient(ellipse 80px 80px at 150px 400px,rgba(240,170,50,.9),rgba(240,170,50,0) 100%),
    radial-gradient(ellipse 100px 60px at 290px 70px,rgba(240,200,90,.8),rgba(240,200,90,0) 100%),
    linear-gradient(135deg,#6a4a2c 0%,#4a3a30 50%,#2c2826 100%)}
.health h2{left:652px;top:80px;font-size:35px;font-weight:700;line-height:42px;color:var(--ink)}
.health .sub{left:652px;top:178px;font-size:19px;font-weight:500;color:var(--honey)}
.health .body{left:652px;top:222px;width:440px;font-size:13px;line-height:22px;color:var(--muted)}

/* social */
.social{top:3047px;height:785px}
.social h2{top:100px;width:1200px;text-align:center;font-size:33px;font-weight:700;color:var(--ink)}
.grid{left:110px;top:158px;width:978px;height:524px;display:grid;grid-template-columns:repeat(3,1fr);grid-template-rows:repeat(2,1fr);gap:2px}
.grid div{width:100%;height:100%}
.p1{background:radial-gradient(ellipse 110px 100px at 45% 60%,#e08a1c,rgba(224,138,28,0) 100%),radial-gradient(ellipse 60px 50px at 55% 20%,#e8a93a,rgba(232,169,58,0) 100%),linear-gradient(160deg,#8a7a66,#5e4a36)}
.p2{background:radial-gradient(ellipse 60px 80px at 40% 65%,#e9e4da,rgba(233,228,218,0) 100%),radial-gradient(ellipse 70px 60px at 62% 40%,#f2f0ec,rgba(242,240,236,0) 100%),linear-gradient(160deg,#4c4c4c,#7e7e7e)}
.p3{background:radial-gradient(ellipse 70px 70px at 72% 45%,rgba(230,190,70,.85),rgba(230,190,70,0) 100%),radial-gradient(ellipse 30px 50px at 50% 80%,rgba(230,190,70,.6),rgba(230,190,70,0) 100%),linear-gradient(160deg,#1a1a1a,#2e2a22)}
.p4{background:radial-gradient(ellipse 70px 100px at 45% 55%,#5a3a20,rgba(90,58,32,0) 100%),radial-gradient(ellipse 60px 90px at 72% 55%,#8a5430,rgba(138,84,48,0) 100%),linear-gradient(160deg,#eeeae4,#c7b29a)}
.p5{background:radial-gradient(ellipse 120px 80px at 50% 58%,#c49a5a,rgba(196,154,90,0) 100%),radial-gradient(ellipse 80px 40px at 50% 60%,#f6f3ee,rgba(246,243,238,0) 100%),linear-gradient(160deg,#f1eee8,#ddd2c0)}
.p6{background:radial-gradient(ellipse 70px 60px at 60% 50%,#f09d2a,rgba(240,157,42,0) 100%),radial-gradient(ellipse 50px 40px at 25% 30%,#e3a53a,rgba(227,165,58,0) 100%),radial-gradient(ellipse 50px 50px at 85% 35%,#f0a83a,rgba(240,168,58,0) 100%),linear-gradient(160deg,#4a3222,#7a5030)}

/* newsletter */
.newsletter{top:3832px;height:299px;background:var(--honey)}
.newsletter h2{top:74px;width:1200px;text-align:center;font-size:33px;font-weight:700;color:var(--ink)}
.newsletter p{top:122px;width:1200px;text-align:center;font-size:14px;color:#222}
.news-form{left:312px;top:158px;width:576px;height:60px;display:flex}
.news-form .field{width:395px;background:var(--white);font-size:15px;color:#333;display:flex;align-items:center;padding-left:26px}
.news-form .submit{flex:1;background:var(--ink);color:var(--white);font-weight:700;font-size:14px;display:flex;align-items:center;justify-content:center}

/* footer */
.footer{top:4131px;height:317px}
.footer h4{font-size:13px;font-weight:700;color:var(--ink);text-decoration:underline;text-transform:uppercase}
.footer ul{list-style:none}
.footer li{font-size:13px;color:#444;height:37px;display:flex;align-items:flex-start;gap:14px}
.footer li b{font-weight:400;color:#777;font-size:12px;width:8px}
.socials{left:779px;top:106px;display:flex;gap:8px}
.socials span{width:30px;height:30px;border:1.5px solid #222;border-radius:50%}
.foot-form{left:779px;top:208px;width:312px;height:50px;border:1px solid var(--line);box-shadow:0 2px 6px rgba(0,0,0,.08);display:flex}
.foot-form .field{flex:1;font-size:13px;color:#555;display:flex;align-items:center;padding-left:16px}
.foot-form .go{width:44px;margin:4px;background:#f2c41a;display:flex;align-items:center;justify-content:center}
.copy{top:4448px;height:73px;background:var(--footer-bar);color:#ddd;font-size:13px;display:flex;align-items:center;justify-content:center}
</style>
</head>
<body>
<div class="page">

<header class="hero" role="img" aria-label="Honey dripping from a wooden dipper into a jar on a rustic table with honeycomb and flowers">
  <div class="abs hero-shade"></div>
  <div class="abs logo">Amber Grove<br>Honey Co.</div>
  <nav class="abs nav">
    <a style="left:21px">HOME</a>
    <a style="left:101px">THE HIVE</a>
    <a style="left:204px">BUY HONEY</a>
    <a style="left:323px">THE BUZZ</a>
    <a style="left:431px">CONTACT US</a>
    <svg style="left:568px" width="15" height="15" viewBox="0 0 16 16"><circle cx="6.5" cy="6.5" r="5" fill="none" stroke="#fff" stroke-width="2"/><line x1="10" y1="10" x2="15" y2="15" stroke="#fff" stroke-width="2"/></svg>
    <svg style="left:610px" width="16" height="15" viewBox="0 0 16 15"><path d="M0 1h3l2 8h9l2-6H4" fill="none" stroke="#fff" stroke-width="2"/><circle cx="6" cy="13" r="1.5" fill="#fff"/><circle cx="13" cy="13" r="1.5" fill="#fff"/></svg>
  </nav>
  <h1 class="abs hero-title">Straight from our<br>beloved hives to your<br>lovely home</h1>
  <span class="btn">Get Started</span>
  <div class="abs dots"><span></span><span></span><span></span></div>
</header>

<section class="importance">
  <h2 class="abs">IMPORTANCE OF BEES:</h2>
  <div class="abs kicker">DON'T JUDGE A BEE BY ITS STINGER</div>
  <p class="abs lead">If the bee disappeared off the face of the Earth, man would have only four years left to live.</p>
  <div class="abs body">
    <p>Hyper-efficient insects do play a vital role in agriculture. Almonds, for example, are almost entirely dependent on honeybee pollination.</p>
    <p>Over one-third of our entire diet is dependent on pollination from the honeybee. So, for every three bites of food you eat, you can thank the honeybee for one of those three bites," Dale says.</p>
    <p>They are very misunderstood among the public. We have lost a great amount of our natural forage land due to urbanization and suburban sprawl, and when people and honeybees mix,</p>
  </div>
  <span class="btn">Learn More</span>
  <div class="abs photo" role="img" aria-label="Honey dipper over a jar of honey beside honeycomb"></div>
</section>

<section class="description">
  <h2 class="abs">OUR DESCRIPTION</h2>
  <p class="abs desc-item left" style="left:112px;top:204px">Halloran, owner of Amber Grove Honey Farm, has about 1,200 beehives that he moves around to pollinate different plants.</p>
  <svg class="abs desc-icon" style="left:404px;top:196px" viewBox="0 0 64 64" role="img" aria-label="Honeycomb cell icon"><g fill="none" stroke="#222" stroke-width="2"><path d="M20 14l10 6v12l-10 6-10-6V20z"/><path d="M40 26l10 6v12l-10 6-10-6V32z"/><path d="M20 38l10 6v12l-10 6-10-6V44z"/></g></svg>
  <svg class="abs desc-icon" style="left:750px;top:196px" viewBox="0 0 64 64" role="img" aria-label="Honey drop icon"><g fill="none" stroke="#222" stroke-width="2"><path d="M32 8C24 22 16 32 16 42a16 16 0 0 0 32 0c0-10-8-20-16-34z"/><path d="M24 44a8 8 0 0 0 8 8"/></g></svg>
  <p class="abs desc-item" style="left:816px;top:204px">100% raw, unfiltered Florida honey straight from the beehives on his six-acre property, Amber Grove Honey Farm, 1840 Orchard Lane in Lakeview.</p>
  <div class="abs desc-photo" role="img" aria-label="Honeycomb with a honey dipper"></div>
  <p class="abs desc-item left" style="left:112px;top:503px">Natural Wild Honey- flavors include Orange Blossom, Gallberry, Summer Wildflower, Winter Wildflower, and many more. Bee Pollen, Royal Jelly, and Bee venom. Bee removals are done by Dale.</p>
  <svg class="abs desc-icon" style="left:402px;top:500px" viewBox="0 0 64 64" role="img" aria-label="Hexagon icon"><g fill="none" stroke="#222" stroke-width="2"><path d="M32 8l20 12v24L32 56 12 44V20z"/><path d="M32 20l10 6v12l-10 6-10-6V26z"/></g></svg>
  <svg class="abs desc-icon" style="left:744px;top:500px" viewBox="0 0 64 64" role="img" aria-label="Field and sun icon"><g fill="none" stroke="#222" stroke-width="2"><circle cx="32" cy="32" r="22"/><path d="M10 36c10-6 34-6 44 0M12 44c10-5 30-5 40 0M18 51c8-3 20-3 28 0"/><circle cx="32" cy="22" r="5"/></g></svg>
  <p class="abs desc-item" style="left:816px;top:503px">Agricultural Company specializing in the Production of 100% Raw American Honey, and the Pollination of America's food crops.</p>
  <svg class="abs desc-icon" style="left:568px;top:584px" viewBox="0 0 64 64" role="img" aria-label="Honey drops icon"><g fill="none" stroke="#222" stroke-width="2"><path d="M32 6c-6 10-12 17-12 25a12 12 0 0 0 24 0c0-8-6-15-12-25z"/><path d="M14 40c-3 5-6 9-6 13a6 6 0 0 0 12 0c0-4-3-8-6-13zM50 40c-3 5-6 9-6 13a6 6 0 0 0 12 0c0-4-3-8-6-13z"/></g></svg>
  <p class="abs desc-item" style="left:395px;top:656px;width:410px;text-align:center">Our Honey comes straight from our beehives to your table. No filtering, heating, or any funny stuff. Just All Natural, 100% Pure Florida Honey</p>
</section>

<section class="video" role="img" aria-label="Two jars of golden honey on a wooden table with a dipper">
  <div class="abs play"><span><svg width="22" height="24" viewBox="0 0 22 24"><path d="M2 1l19 11L2 23z" fill="#111"/></svg></span></div>
</section>

<section class="health">
  <div class="abs photo" role="img" aria-label="Jars of honey, bee pollen and honeycomb on a dark board"></div>
  <h2 class="abs">THE HEALTH BENEFITS<br>OF HONEY</h2>
  <div class="abs sub">REAL LOCAL HONEY, REALLY GOOD FOR YOU</div>
  <p class="abs body">Raw honey is loaded with antioxidants to protect your body from cell damage due to free radicals. Honey has been long known as a folk remedy to help heal burns and wounds due to its antibacterial and antifungal properties. Honey is also very well known to soothe a sore throat. Try taking a spoonful of honey and add it to hot tea if you feel like you have a cold. Honey can also help as a cough suppressant.</p>
</section>

<section class="social">
  <h2 class="abs">SOCIAL MEDIA POSTS</h2>
  <div class="abs grid">
    <div class="p1" role="img" aria-label="Honey dipper resting in a jar"></div>
    <div class="p2" role="img" aria-label="Honey jar with gift box packaging"></div>
    <div class="p3" role="img" aria-label="Black and gold honey gift boxes"></div>
    <div class="p4" role="img" aria-label="Honeycomb frame with a honey bottle"></div>
    <div class="p5" role="img" aria-label="Three honey bottles in a wooden box"></div>
    <div class="p6" role="img" aria-label="Bowls of honey and bee pollen"></div>
  </div>
</section>

<section class="newsletter">
  <h2 class="abs">NEWSLETTER</h2>
  <p class="abs">Sign up to receive 15% off your first order.</p>
  <div class="abs news-form"><span class="field">Email address</span><span class="submit">SUBSCRIBE</span></div>
</section>

<footer class="footer">
  <div class="abs" style="left:110px;top:80px">
    <h4>Quick Links</h4>
    <ul style="margin-top:18px">
      <li><b>»</b>Home</li><li><b>»</b>About Us</li><li><b>»</b>Our Products</li><li><b>»</b>Reviews</li><li><b>»</b>Latest Blog</li>
    </ul>
  </div>
  <div class="abs" style="left:295px;top:80px">
    <h4>Other Links</h4>
    <ul style="margin-top:18px">
      <li><b>»</b>Terms &amp; Conditions</li><li><b>»</b>Privacy Policy</li><li><b>»</b>Help Service</li><li><b>»</b>FAQ</li><li><b>»</b>Contact us</li>
    </ul>
  </div>
  <div class="abs" style="left:526px;top:80px">
    <h4>Find Us On</h4>
    <ul style="margin-top:18px">
      <li><svg width="10" height="14" viewBox="0 0 10 14"><path d="M5 0a5 5 0 0 1 5 5c0 4-5 9-5 9S0 9 0 5a5 5 0 0 1 5-5z" fill="#555"/><circle cx="5" cy="5" r="2" fill="#fff"/></svg><span style="margin-left:6px">48 , Meadow Street</span></li>
      <li style="padding-left:30px">United States</li>
      <li><svg width="12" height="12" viewBox="0 0 12 12"><path d="M2 0l3 3-1.5 2a7 7 0 0 0 3.5 3.5L9 7l3 3-2 2C5 12 0 7 0 2z" fill="#555"/></svg><span style="margin-left:4px">1 555 010 2040</span></li>
      <li><svg width="13" height="10" viewBox="0 0 13 10"><rect x=".5" y=".5" width="12" height="9" fill="none" stroke="#555"/><path d="M.5 .5l6 5 6-5" fill="none" stroke="#555"/></svg><span style="margin-left:3px">hello@ambergrove.example</span></li>
    </ul>
  </div>
  <div class="abs" style="left:779px;top:70px"><h4>Connected Us On</h4></div>
  <div class="abs socials"><span></span><span></span><span></span><span></span><span></span></div>
  <div class="abs" style="left:779px;top:178px"><h4>Subscribe to our newsletter</h4></div>
  <div class="abs foot-form"><span class="field">Email Address</span><span class="go"><svg width="16" height="16" viewBox="0 0 16 16"><path d="M15 1L1 7l6 2 2 6z" fill="#111"/></svg></span></div>
</footer>

<div class="abs copy" style="left:0;width:1200px">© 2021 Company name. All Rights Reserved</div>

</div>
</body>
</html>
```